Small Business Broker Business Card Design

A business card design for a small business brokerage, which is a financial service, not unlike real estate brokerage, but for small businesses such as laundromats, pizza shops, restaurants, cleaners etc. The designs should all be simple, more conservative in nature, using the colors and font of the logo. Again, think real estate Brokerage as a business context
Contact Information for Business Card
Name: Glen R. Harlow. Title: Small Business Advisor. Email: g.harlow@bayfieldcapitalworks.example. Mobile: (555) 274-3918. Office: (555) 806-2147. www.bayfieldcapitalworks.example

```html
<!DOCTYPE html>
<html lang="en">
<head>
<meta charset="utf-8">
<title>Bayfield Capital Works – Business Card</title>
<link rel="stylesheet" href="https://fonts.googleapis.com/css2?family=Montserrat:wght@700;800&family=Arimo:ital,wght@0,400;1,400&display=swap">
<style>
  :root {
    --stage: #1b1c1f;
    --navy: #142d62;
    --navy-deep: #10265a;
    --navy-light: #1a3a78;
    --white: #ffffff;
    --green: #6cbf2f;
    --faint: rgba(120, 150, 200, 0.18);
  }
  * { box-sizing: border-box; margin: 0; padding: 0; }
  html, body {
    width: 1200px; height: 963px; overflow: hidden;
    background: var(--stage);
  }
  .sheet {
    width: 1200px; height: 963px;
    display: flex; flex-direction: column; align-items: center; justify-content: center;
    gap: 56px;
  }
  .card {
    position: relative;
    width: 700px; height: 400px;
    border-radius: 28px;
    overflow: hidden;
    background: linear-gradient(135deg, var(--navy-deep) 0%, var(--navy) 55%, var(--navy-light) 100%);
    box-shadow: 0 18px 40px rgba(0,0,0,0.55);
  }
  .company-name {
    font-family: "Montserrat", sans-serif;
    font-weight: 800;
    text-transform: uppercase;
    letter-spacing: 0.09em;
    color: var(--white);
  }
  .tagline {
    font-family: "Montserrat", sans-serif;
    font-weight: 700;
    text-transform: uppercase;
    letter-spacing: 0.12em;
    color: var(--green);
  }

  /* Front */
  .card-front .brand { position: absolute; left: 44px; top: 42px; }
  .card-front .company-name { font-size: 22px; }
  .card-front .tagline { font-size: 10.5px; margin-top: 5px; }
  .person { position: absolute; left: 44px; top: 128px; }
  .person-name {
    font-family: "Montserrat", sans-serif; font-weight: 800;
    font-size: 27px; letter-spacing: 0.05em; text-transform: uppercase;
    color: var(--white);
  }
  .person-title {
    font-family: "Arimo", sans-serif; font-style: italic;
    font-size: 17px; color: var(--green); margin-top: 2px;
  }
  .contact-list {
    position: absolute; left: 44px; top: 228px;
    list-style: none;
    font-family: "Arimo", sans-serif; font-size: 17px; color: var(--white);
  }
  .contact-list li { display: flex; align-items: center; gap: 10px; height: 28px; }
  .contact-list svg { width: 16px; height: 16px; flex: none; }
  .faint-accent {
    position: absolute; right: 0; bottom: 0;
    width: 360px; height: 230px;
    background: radial-gradient(ellipse at 70% 70%, var(--faint) 0%, rgba(120,150,200,0.06) 55%, transparent 80%);
  }

  /* Back */
  .card-back .pattern {
    position: absolute; inset: 0;
    background: linear-gradient(135deg, #112a5e 0%, #1a3a78 50%, #142d62 100%);
  }
  .card-back .brand {
    position: absolute; left: 0; right: 0; top: 50%;
    transform: translateY(-50%);
    display: flex; align-items: center; justify-content: center; gap: 18px;
  }
  .brand-square { width: 34px; height: 34px; background: var(--green); flex: none; }
  .card-back .company-name { font-size: 25px; }
  .card-back .tagline { font-size: 12px; margin-top: 6px; }
</style>
</head>
<body>
<main class="sheet">

  <section class="card card-front" aria-label="Business card front">
    <div class="brand">
      <p class="company-name">Bayfield Capital Works, Inc</p>
      <p class="tagline">Confidently buy or sell a local business today</p>
    </div>

    <div class="person">
      <h1 class="person-name">Glen R. Harlow</h1>
      <p class="person-title">Small Business Advisor</p>
    </div>

    <ul class="contact-list">
      <li>
        <svg viewBox="0 0 16 16" aria-hidden="true"><path d="M3.5 1.5l2.5 0 1 3.2-1.6 1.2a8 8 0 0 0 4.7 4.7l1.2-1.6 3.2 1v2.5a1.5 1.5 0 0 1-1.6 1.5A12.5 12.5 0 0 1 2 3.1 1.5 1.5 0 0 1 3.5 1.5z" fill="var(--green)"/></svg>
        (555) 806-2147
      </li>
      <li>
        <svg viewBox="0 0 16 16" aria-hidden="true"><rect x="4" y="1" width="8" height="14" rx="1.5" fill="none" stroke="var(--green)" stroke-width="1.5"/><circle cx="8" cy="12.5" r="0.9" fill="var(--green)"/></svg>
        (555) 274-3918
      </li>
      <li>
        <svg viewBox="0 0 16 16" aria-hidden="true"><rect x="1.5" y="3.5" width="13" height="9" rx="1" fill="none" stroke="var(--green)" stroke-width="1.5"/><path d="M2 4l6 5 6-5" fill="none" stroke="var(--green)" stroke-width="1.5"/></svg>
        g.harlow@bayfieldcapitalworks.example
      </li>
      <li>
        <svg viewBox="0 0 16 16" aria-hidden="true"><circle cx="8" cy="8" r="6.3" fill="none" stroke="var(--green)" stroke-width="1.4"/><ellipse cx="8" cy="8" rx="2.8" ry="6.3" fill="none" stroke="var(--green)" stroke-width="1.2"/><path d="M1.8 8h12.4M2.8 5h10.4M2.8 11h10.4" stroke="var(--green)" stroke-width="1.1"/></svg>
        www.bayfieldcapitalworks.example
      </li>
    </ul>

    <div class="faint-accent" role="img" aria-label="Faint large brand decoration in the lower right corner"></div>
  </section>

  <section class="card card-back" aria-label="Business card back">
    <div class="pattern" role="img" aria-label="Embossed repeating brand pattern across the card"></div>
    <div class="brand">
      <span class="brand-square" aria-hidden="true"></span>
      <div>
        <p class="company-name">Bayfield Capital Works, Inc</p>
        <p class="tagline">Confidently buy or sell a local business today</p>
      </div>
    </div>
  </section>

</main>
</body>
</html>
```